Business Card for Vorla Parts Wholesale supplier

Hi There! I need a new business card for our company. We are specialized in selling Vorla parts, mostly we sell new LCD screens for Zelnar and Drelks. I would like to see that back in the design.

You can find the colors and logo's on our website: www.hartuvo.nl

Industry/Entity Type

Business

Contact Information for Business Card

My Details:
Tobias Lindqvist

Phone: 0031687203316
E-mail: Tobias@hartuvo.nl

Slogan: "Because Quality Matters"

Font styles to use
Sans Serif

Colors

Designer to choose colors to be used in the design.

Requirements
Must have
• A Black backside with the Hartuvo logo on it. The front side should be clean with only my contact details.
• But I'm also open for something really different or awesome!
Nice to have
• Remember that we are in the parts & repairing industry, So i'll be handing those business cards mainly to repair companies. Maybe you can do something with that thought :)

```html
<!DOCTYPE html>
<html lang="en">
<head>
<meta charset="utf-8">
<title>Hartuvo Business Card</title>
<link href="https://fonts.googleapis.com/css2?family=Exo+2:wght@300;500;600&family=PT+Sans:wght@700&display=swap" rel="stylesheet">
<style>
  :root {
    --backdrop: #5a4a3c;
    --paper: #ffffff;
    --ink: #000000;
    --brand-orange: #f47424;
    --contact-text: #ffffff;
  }
  html, body {
    margin: 0;
    width: 1200px;
    height: 987px;
    overflow: hidden;
    background: var(--backdrop);
  }
  .card {
    position: absolute;
    width: 616px;
    height: 352px;
    display: block;
  }
  .card--front { left: 293px; top: 130px; }
  .card--back  { left: 292px; top: 505px; }
  .wordmark {
    font-family: "Exo 2", sans-serif;
    font-weight: 600;
  }
  .contact-line {
    font-family: "Exo 2", sans-serif;
    font-weight: 300;
    font-size: 13px;
    fill: var(--contact-text);
  }
  .holder-name {
    font-family: "Exo 2", sans-serif;
    font-weight: 600;
    font-size: 24px;
    fill: var(--brand-orange);
    letter-spacing: 0.5px;
  }
  .slogan {
    font-family: "PT Sans", sans-serif;
    font-weight: 700;
    font-size: 14.5px;
    fill: var(--paper);
  }
  .icon { fill: var(--brand-orange); }
</style>
</head>
<body>

<!-- Front: contact side -->
<svg class="card card--front" viewBox="0 0 525 300" xmlns="http://www.w3.org/2000/svg" aria-label="Business card front with contact details">
  <rect class="card-base" width="525" height="300" fill="var(--paper)"/>
  <polygon class="accent-stripe" points="417,0 525,0 525,300 95,300" fill="var(--brand-orange)"/>
  <polygon class="dark-panel" points="431,0 525,0 525,300 108,300" fill="var(--ink)"/>

  <g class="brand">
    <rect x="44" y="52" width="34" height="34" fill="var(--brand-orange)"/>
    <text class="wordmark" x="88" y="84" font-size="42" fill="var(--ink)">hartuvo</text>
  </g>

  <g class="contacts" text-anchor="end">
    <text class="contact-line" x="470" y="182">0031687203316</text>
    <text class="contact-line" x="470" y="202">Tobias@hartuvo.nl</text>
    <text class="contact-line" x="470" y="222">www.hartuvo.nl</text>
  </g>

  <g class="contact-icons">
    <path class="icon icon-phone" d="M478,172 l3,-1 l2,4 l-2,1.5 q1.5,3 4,4.5 l1.5,-2 l4,2 l-1,3 q-7,0 -11.5,-12 z"/>
    <g class="icon-mail">
      <rect class="icon" x="477" y="193" width="13" height="9"/>
      <path d="M477,193 l6.5,5 l6.5,-5" fill="none" stroke="var(--ink)" stroke-width="1.2"/>
    </g>
    <g class="icon-globe">
      <circle class="icon" cx="483.5" cy="218" r="6"/>
      <path d="M477.5,218 h12 M483.5,212 q-4,6 0,12 M483.5,212 q4,6 0,12" fill="none" stroke="var(--ink)" stroke-width="1"/>
    </g>
  </g>

  <text class="holder-name" x="489" y="257" text-anchor="end">Tobias Lindqvist</text>
</svg>

<!-- Back: brand side -->
<svg class="card card--back" viewBox="0 0 525 300" xmlns="http://www.w3.org/2000/svg" aria-label="Business card back with brand name and slogan">
  <rect class="card-base" width="525" height="300" fill="var(--brand-orange)"/>
  <text class="wordmark" x="496" y="254" font-size="44" fill="var(--paper)" text-anchor="end">hartuvo</text>
  <text class="slogan" x="496" y="280" text-anchor="end">Because Quality Matters</text>
</svg>

</body>
</html>
```